Fun relaxed Travel Photography Business Card*

Require a fun, funky and quirky but rememberable business card for a travel photographer

Industry/Entity Type

Photographer

Contact Information for Business Card

Front Card

(my name) Lenn D.

Travel Photographer ( small under travel photographer) “self-proclaimed”

(website logo) wanderingsoflenn.net

(Instagram logo) @wanderings_of_lenn

(Instagram logo) @wanderings_of_lenn_2.0 (backup for when Instagram puts Lenn on timeout for bad behaviour)

Tel: N/A (removing the potential awkwardness of me not replying)

Email: (see above)

Back Card

Offending people since 1986

(Bottom right corner) “p.s. travelling made me fatTER”

Font styles to use
Serif

Colors

Designer to choose colors to be used in the design.

Requirements
Must have
• a camera
• a similar cartoon version of me as the "logo" see attached files, try to make as similar as possible

```html
<!DOCTYPE html>
<html lang="en">
<head>
<meta charset="UTF-8">
<title>Lenn D. — Travel Photographer Business Card</title>
<link href="https://fonts.googleapis.com/css2?family=Montserrat:wght@400;500;700&display=swap" rel="stylesheet">
<style>
  :root {
    --backdrop: #2b2d31;
    --card-white: #ffffff;
    --brand-blue: #44668f;
    --brand-blue-dark: #3a5a80;
    --line-white: #f4f6f9;
    --text-grey: #6a6d72;
    --text-white: #ffffff;
    --skin: #5a3520;
    --shirt: #2b3f9a;
  }
  * { box-sizing: border-box; margin: 0; padding: 0; }
  html, body { width: 1200px; height: 900px; overflow: hidden; }
  body {
    background: var(--backdrop);
    font-family: "Montserrat", sans-serif;
    position: relative;
  }
  .card {
    position: absolute;
    left: 320px;
    width: 560px;
    height: 320px;
    overflow: hidden;
  }
  .card--front { top: 100px; background: var(--card-white); }
  .card--back {
    top: 480px;
    background: linear-gradient(135deg, var(--brand-blue) 0%, var(--brand-blue-dark) 100%);
  }
  .frame-lines { position: absolute; inset: 0; width: 560px; height: 320px; }
  .portrait {
    position: absolute;
    background: radial-gradient(ellipse at 55% 40%, var(--skin) 0%, var(--skin) 38%, var(--shirt) 62%, rgba(43,63,154,0) 78%);
  }
  .card--front .portrait { left: 60px; top: 36px; width: 130px; height: 154px; }
  .card--back .portrait { left: 235px; top: 44px; width: 110px; height: 140px; }

  .contact-list {
    position: absolute;
    left: 30px;
    top: 212px;
    list-style: none;
    color: var(--text-grey);
    font-size: 13px;
    line-height: 19px;
  }
  .contact-list li { display: flex; align-items: center; gap: 7px; }
  .contact-icon { width: 11px; height: 11px; flex: none; }
  .contact-icon--square { border: 1.5px solid var(--brand-blue); border-radius: 2px; }

  .name-band {
    position: absolute;
    left: 262px;
    right: 0;
    top: 132px;
    height: 34px;
    background: var(--brand-blue);
    color: var(--text-white);
    display: flex;
    align-items: center;
    padding-left: 22px;
    gap: 10px;
  }
  .name-band__name { font-weight: 700; font-size: 20px; }
  .name-band__divider { width: 2px; height: 20px; background: var(--text-white); }
  .name-band__title { font-weight: 500; font-size: 14px; letter-spacing: 0.3px; }
  .tagline-small {
    position: absolute;
    left: 400px;
    top: 176px;
    font-size: 12px;
    color: var(--text-grey);
  }

  .back-text {
    position: absolute;
    left: 0;
    right: 0;
    top: 200px;
    text-align: center;
    color: var(--text-white);
    font-size: 13px;
    line-height: 19px;
    letter-spacing: 0.4px;
  }
</style>
</head>
<body>

  <section class="card card--front" aria-label="Business card front">
    <svg class="frame-lines" viewBox="0 0 560 320" aria-hidden="true">
      <path d="M100 30 H30 V175" fill="none" stroke="#44668f" stroke-width="1.6"/>
      <path d="M230 95 V198 H125" fill="none" stroke="#44668f" stroke-width="1.6"/>
    </svg>
    <div class="portrait" role="img" aria-label="Cartoon avatar of Lenn in sunglasses and a floral shirt"></div>

    <ul class="contact-list">
      <li><span class="contact-icon contact-icon--square"></span>@wanderings_of_lenn</li>
      <li><span class="contact-icon contact-icon--square"></span>@wanderings_of_lenn_2.0</li>
      <li>
        <svg class="contact-icon" viewBox="0 0 12 12" aria-hidden="true">
          <rect x="0.5" y="2" width="11" height="8" fill="#44668f"/>
          <path d="M0.5 2 L6 7 L11.5 2" fill="none" stroke="#fff" stroke-width="1"/>
        </svg>lenn.wanders@postmail.net
      </li>
      <li>
        <svg class="contact-icon" viewBox="0 0 12 12" aria-hidden="true">
          <circle cx="6" cy="6" r="5.3" fill="#44668f"/>
          <ellipse cx="6" cy="6" rx="2.2" ry="5.3" fill="none" stroke="#fff" stroke-width="0.8"/>
          <line x1="0.7" y1="6" x2="11.3" y2="6" stroke="#fff" stroke-width="0.8"/>
        </svg>www.wanderingsoflenn.net
      </li>
    </ul>

    <div class="name-band">
      <span class="name-band__name">Lenn D.</span>
      <span class="name-band__divider"></span>
      <span class="name-band__title">Travel Photographer</span>
    </div>
    <p class="tagline-small">self-proclaimed</p>
  </section>

  <section class="card card--back" aria-label="Business card back">
    <svg class="frame-lines" viewBox="0 0 560 320" aria-hidden="true">
      <path d="M272 34 H208 V150" fill="none" stroke="#f4f6f9" stroke-width="1.4"/>
      <path d="M372 90 V192 H300" fill="none" stroke="#f4f6f9" stroke-width="1.4"/>
      <line x1="0" y1="209" x2="165" y2="209" stroke="#f4f6f9" stroke-width="1.4"/>
      <line x1="398" y1="228" x2="560" y2="228" stroke="#f4f6f9" stroke-width="1.4"/>
    </svg>
    <div class="portrait" role="img" aria-label="Cartoon avatar of Lenn in sunglasses and a floral shirt"></div>
    <div class="back-text">
      <p>Offending people since 1986</p>
      <p>p.s. travelling made me fatTER</p>
    </div>
  </section>

</body>
</html>
```